Counseling Practice Business Card

I need a professional looking business card incorporating my new logo that was just completed. Card needs to incorporate my name and title, description of my specialty, my address, my phone number, my fax number, my email and my website URL. I need to be able to choose design on/with different paper colors and textures.
I do not have a lot of business card ideas so I am open to anything but I want bold,sharp, clear card without additional designs other than my logo (see attached file info). I am open to different color backgrounds or paper colors including black. I do not like traditional brackets around area codes in phone number or dashes between numbers in phone number. Am open to other ways of presenting including periods between numbers as appropriate. I do not know enough to know what I like yet but I want card to coordinate and work together with my logo. My practice emphasizes natural mental health interventions so any use of color (with background paper color or the blue and green in my logo) that elicits nature is nice. In addition to black, any natural brown or wood looking background might be desirable also. Most of the offerings so far look very similar and boring.

Target Market(s)

Potential therapy clients and other professionals

Contact Information for Business Card

Card information:
Gerald M. Whitcombe, Ph.D.
Licensed Clinical Psychologist
Integrative Health Coach
4812 Marlowe Ridge Blvd SE
Suite 310
Fernhaven, GA 30512
(770) 415-2983 phone
(770) 581-4096 fax
drgeraldwhitcombe@quillmarsh.net
brightfernwellness.net

Font styles to use
Serif
Sans Serif
Other font styles liked:
• anything that you think looks crisp, clear and easily readable

Requirements
Must have
• Any color used should coordinate with my logo design (see attached files).
• Card should be printed horizontally so top and bottom are longest sides of rectangle.
• Background color or paper color should complement and highlight logo. Do not like a white background. black, grey, brown or any color my logo would blend well with.
Nice to have
• I would like designer to utilize color to highlight letters/name or phone-fax-web symbols.
• Bottom edge of card could be highlighted if appropriate to an idea.
Should not have
• I would NOT want the card to have a pure white background at all.
• No clear cards.
• Cards should be oriented with long sides on bottom and top, NOT sides. DO NOT LIKE THIS THIN TALL ORIENTATION.

```html
<!DOCTYPE html>
<html lang="en">
<head>
<meta charset="utf-8">
<title>Brightfern Wellness – Business Card</title>
<link href="https://fonts.googleapis.com/css2?family=Roboto:wght@400;500&family=Roboto+Condensed:wght@500;600&display=swap" rel="stylesheet">
<style>
  :root {
    --backdrop: #c99a66;
    --card: #141518;
    --brand-blue: #2a74b8;
    --brand-green: #1e7a3c;
    --text-light: #d0d1d4;
    --rule: #5a5c61;
    --band-text: #ffffff;
    --band-text-soft: #c4d3e6;
  }
  * { margin: 0; padding: 0; box-sizing: border-box; }
  html, body { width: 1200px; height: 960px; overflow: hidden; }
  body {
    position: relative;
    background: var(--backdrop);
    font-family: "Roboto", Arial, sans-serif;
  }
  .card {
    position: absolute;
    width: 600px;
    height: 342px;
    background: var(--card);
    overflow: hidden;
  }
  .card--front { left: 314px; top: 113px; }
  .card--back { left: 311px; top: 472px; height: 343px; }

  .brand-name {
    position: absolute;
    color: var(--brand-blue);
    font-family: "Roboto", Arial, sans-serif;
    font-weight: 500;
    text-align: center;
    line-height: 1;
  }
  .brand-name .brand-main { display: block; }
  .brand-name .brand-sub { display: block; letter-spacing: 6px; text-transform: uppercase; }

  .card--front .brand-name { left: 30px; top: 142px; width: 230px; }
  .card--front .brand-main { font-size: 38px; }
  .card--front .brand-sub { font-size: 15px; margin-top: 8px; }

  .card--back .brand-name { left: 0; top: 125px; width: 600px; }
  .card--back .brand-main { font-size: 62px; }
  .card--back .brand-sub { font-size: 22px; margin-top: 8px; letter-spacing: 9px; }

  .divider {
    position: absolute;
    left: 283px; top: 62px;
    width: 1px; height: 206px;
    background: linear-gradient(to bottom, transparent, var(--rule) 20%, var(--rule) 80%, transparent);
  }
  .contact { position: absolute; left: 311px; top: 70px; }
  .contact-name {
    font-family: "Roboto Condensed", Arial, sans-serif;
    font-weight: 600;
    font-size: 21px;
    color: var(--brand-blue);
    text-transform: uppercase;
    line-height: 1.1;
  }
  .contact-title {
    font-family: "Roboto", Arial, sans-serif;
    font-weight: 400;
    font-size: 15px;
    color: var(--brand-green);
    line-height: 19px;
  }
  .address {
    margin-top: 8px;
    font-size: 14px;
    line-height: 18px;
    color: var(--text-light);
    font-style: normal;
  }
  .contact-lines { list-style: none; margin-top: 10px; }
  .contact-lines li {
    display: flex; align-items: center;
    font-size: 14px; line-height: 19px;
    color: var(--text-light);
  }
  .contact-lines svg { width: 13px; height: 13px; margin-right: 10px; fill: var(--brand-blue); }

  .bands { position: absolute; left: 0; top: 0; width: 600px; height: 342px; }
  .front-url {
    position: absolute;
    left: 0; top: 318px; width: 390px; height: 24px;
    text-align: center;
    line-height: 24px;
    font-size: 14px; font-weight: 500;
    letter-spacing: 3px;
    color: var(--band-text);
  }
  .back-band {
    position: absolute;
    left: 0; top: 279px; width: 600px; height: 30px;
    background: var(--brand-blue);
    text-align: center;
    line-height: 30px;
    font-size: 14px; letter-spacing: 4px;
    color: var(--band-text-soft);
  }
</style>
</head>
<body>

<section class="card card--front">
  <div class="brand-name"><span class="brand-main">Brightfern</span><span class="brand-sub">Wellness</span></div>
  <div class="divider"></div>
  <div class="contact">
    <h1 class="contact-name">Gerald M. Whitcombe, Ph.D.</h1>
    <p class="contact-title">Licensed Clinical Psychologist</p>
    <p class="contact-title">Integrative Health Coach</p>
    <address class="address">4812 Marlowe Ridge Blvd SE<br>Suite 310<br>Fernhaven, GA 30512</address>
    <ul class="contact-lines">
      <li><svg viewBox="0 0 16 16" aria-hidden="true"><path d="M3.6 1.2l2.3 2.4-1.4 2a9 9 0 0 0 5.9 5.9l2-1.4 2.4 2.3-1.6 2.4C7.4 14.8 1.2 8.6 1.2 2.8z"/></svg>(770) 415-2983</li>
      <li><svg viewBox="0 0 16 16" aria-hidden="true"><path d="M4 1h8v4H4zM1 6h14v7h-3v-3H4v3H1zM5 11h6v4H5z"/></svg>(770) 581-4096</li>
      <li><svg viewBox="0 0 16 16" aria-hidden="true"><path d="M1 3h14v1.5L8 9 1 4.5zM1 6.3l7 4.5 7-4.5V13H1z"/></svg>drgeraldwhitcombe@quillmarsh.net</li>
    </ul>
  </div>
  <svg class="bands" viewBox="0 0 600 342" aria-hidden="true">
    <polygon points="391,328 600,328 600,342 398,342" fill="var(--brand-blue)"/>
    <polygon points="0,318 383,318 396,342 0,342" fill="var(--brand-green)"/>
  </svg>
  <div class="front-url">www.brightfernwellness.net</div>
</section>

<section class="card card--back">
  <div class="brand-name"><span class="brand-main">Brightfern</span><span class="brand-sub">Wellness</span></div>
  <div class="back-band">www.brightfernwellness.net</div>
</section>

</body>
</html>
```